Vorn upkeep KT Solar Venture

Solar power system install
Services and maintenance
wiring, Rewinding and Renovation
Switch Board Upgrade
Power and lighting point
t doesn’t matter how much you spend on quality parts, your solar system will let you down if your design and installation are sub-par. Have your solar system tailored and installed by our Master Electrician and Bright Grid Guild Accredited team.

Target Market(s)

sales and installed

Industry/Entity Type

Solar install and retailer

Contact Information for Business Card

Name , Email, Phone Number ,Business address,

Font styles to use
Serif

Colors
0054AA
0677BA
7BADD7
CADEEF
E8F1F8

Requirements
Must have
• clear and bright
Nice to have
• new design
Should not have
• unclear pictures

```html
<!DOCTYPE html>
<html lang="en">
<head>
<meta charset="utf-8">
<title>Vorn Upkeep KT Solar Venture – Business Card</title>
<link rel="stylesheet" href="https://fonts.googleapis.com/css2?family=Roboto:wght@400;500;700;900&display=swap">
<style>
  :root {
    --blue-deep: #0054AA;
    --blue-mid: #0677BA;
    --blue-light: #7BADD7;
    --blue-pale: #CADEEF;
    --blue-mist: #E8F1F8;
    --green: #3C9B2E;
    --green-dark: #1F7A2E;
    --sun: #F2A91F;
    --ink: #1d1d1d;
    --paper: #F1F1F1;
    --backdrop: #2E2E2E;
  }
  * { margin: 0; padding: 0; box-sizing: border-box; }
  html, body { width: 1200px; height: 1138px; overflow: hidden; }
  body {
    background: var(--backdrop);
    font-family: "Roboto", Arial, sans-serif;
    position: relative;
  }
  .card {
    position: absolute;
    left: 277px;
    width: 622px;
    height: 375px;
    border-radius: 16px;
    overflow: hidden;
  }
  .card-front { top: 186px; background: linear-gradient(160deg, var(--blue-deep), var(--blue-mid)); }
  .card-back { top: 608px; background: var(--paper); }

  .front-art { position: absolute; inset: 0; }

  .brand { position: absolute; display: flex; align-items: center; }
  .brand-dot { border-radius: 50%; flex: none; }
  .brand-name {
    font-weight: 900;
    text-transform: uppercase;
    line-height: 1.05;
    letter-spacing: 0.5px;
  }
  .card-front .brand { left: 298px; top: 62px; gap: 14px; }
  .card-front .brand-dot { width: 62px; height: 62px; background: var(--sun); }
  .card-front .brand-name { color: #fff; font-size: 27px; }

  .services {
    position: absolute;
    right: 30px;
    top: 222px;
    list-style: none;
    text-align: right;
    color: #fff;
    font-size: 17px;
    line-height: 22.4px;
  }
  .services li::after { content: "«"; margin-left: 10px; }

  .card-back .brand { left: 16px; top: 40px; gap: 18px; }
  .card-back .brand-dot { width: 92px; height: 92px; background: var(--sun); }
  .card-back .brand-name { color: var(--blue-deep); font-size: 36px; }

  .person { position: absolute; left: 34px; top: 204px; }
  .person-name { color: var(--blue-deep); font-size: 26px; font-weight: 500; }
  .person-role { color: var(--ink); font-size: 16px; margin-top: 3px; }

  .divider { position: absolute; left: 0; top: 236px; }

  .contacts { position: absolute; left: 32px; top: 280px; list-style: none; }
  .contacts li {
    display: flex; align-items: center; gap: 18px;
    font-size: 17px; color: var(--ink); height: 24px;
  }
  .contacts svg { width: 16px; height: 16px; flex: none; }

  .address {
    position: absolute; right: 34px; top: 304px;
    text-align: right; font-size: 17px; color: var(--ink); line-height: 24px;
    font-style: normal;
  }
</style>
</head>
<body>

<section class="card card-front">
  <svg class="front-art" width="622" height="375" viewBox="0 0 622 375">
    <defs>
      <linearGradient id="panel-tone" x1="0" y1="0" x2="1" y2="1">
        <stop offset="0" stop-color="#6F7C93"/>
        <stop offset="0.45" stop-color="#B89A86"/>
        <stop offset="1" stop-color="#2C3346"/>
      </linearGradient>
    </defs>
    <path d="M0 0 H212 Q356 188 208 375 H0 Z" fill="var(--green)"/>
    <path d="M0 0 H204 Q346 188 200 375 H0 Z" fill="url(#panel-tone)" role="img" aria-label="Photo of solar panels catching sunlight"/>
  </svg>

  <div class="brand">
    <span class="brand-dot"></span>
    <span class="brand-name">Vorn Upkeep<br>KT Solar Venture</span>
  </div>

  <ul class="services">
    <li>Solar Power System Install</li>
    <li>Services &amp; Maintenance</li>
    <li>Switch Board Upgrade</li>
    <li>Power &amp; Lighting Point</li>
    <li>Wiring, Rewinding &amp; Renovation</li>
  </ul>
</section>

<section class="card card-back">
  <div class="brand">
    <span class="brand-dot"></span>
    <span class="brand-name">Vorn Upkeep<br>KT Solar Venture</span>
  </div>

  <div class="person">
    <div class="person-name">Mara Quell Ostin</div>
    <div class="person-role">Managing Director</div>
  </div>

  <svg class="divider" width="622" height="40" viewBox="0 0 622 40">
    <path d="M30 28 H236 C262 28 262 10 292 10 H588" fill="none" stroke="#6DB33F" stroke-width="2"/>
  </svg>

  <ul class="contacts">
    <li>
      <svg viewBox="0 0 16 16"><path d="M3 2 L6 2 L7 5 L5 6.5 C6 9 7 10 9.5 11 L11 9 L14 10 L14 13 C14 14 13 14.5 12 14.5 C6 14 2 10 1.5 4 C1.5 3 2 2 3 2 Z" fill="var(--green-dark)"/></svg>
      <span>555-014-2290</span>
    </li>
    <li>
      <svg viewBox="0 0 16 16"><rect x="1" y="3" width="14" height="10" fill="var(--green-dark)"/><path d="M1.5 3.5 L8 9 L14.5 3.5" fill="none" stroke="#fff" stroke-width="1.3"/></svg>
      <span>mara@vornupkeep.com</span>
    </li>
    <li>
      <svg viewBox="0 0 16 16"><circle cx="8" cy="8" r="6.5" fill="none" stroke="var(--green-dark)" stroke-width="1.4"/><ellipse cx="8" cy="8" rx="2.8" ry="6.5" fill="none" stroke="var(--green-dark)" stroke-width="1.2"/><path d="M1.5 8 H14.5 M2.5 5 H13.5 M2.5 11 H13.5" stroke="var(--green-dark)" stroke-width="1.1"/></svg>
      <span>www.vornupkeep.com</span>
    </li>
  </ul>

  <address class="address">87 Larkfield Rd., Dunmore Vale,<br>Eastbrook, US 40219</address>
</section>

</body>
</html>
```